Modern Homepage Design for brenvik.nl – Fish & Chicken Food Webshop

Brenvik.nl is an online store that sells fish and chicken food. The design should be visually appealing, easy to navigate, and optimized for e-commerce. We want a layout that helps customers quickly find what they need and encourages them to explore our products.
A good example of the style and structure we like is dierkamp.nl – clean layout, clear product focus, and user-friendly navigation.
Brand Colors (must be used):
Orange: #f7a441
Dark Gray: #3c3c3b
White: #ffffff
Please use these colors consistently throughout the design.
Homepage Requirements:
The homepage should include the following sections:
Main Slider / Hero Banner
A large, eye-catching slider at the top of the page to highlight promotions or featured categories.
Category Blocks
A section with clear, clickable blocks or tiles that link to main product categories (e.g., Fish Food, Chicken Food, Accessories).
Featured Products
A section showcasing selected or best-selling products.
Special Offers / Promotions
A space to highlight current deals or limited-time offers.
Three Banners in a Row
A section with three horizontal banners side by side, which can be used for promotions, shipping info, or other key messages.
Unique Selling Points (USPs)
A section that briefly explains what makes our store different (e.g., fast delivery, high-quality feed, trusted by professionals).
SEO Content Block
A short paragraph of text for SEO purposes (use Lorem Ipsum for dummy content).
Footer Design
Include space for contact information, navigation links, and social media.
Design Notes:
The design must be responsive and mobile-friendly.
Focus on clean layout, good spacing, and easy navigation.
Use modern fonts and a clear visual hierarchy.
We are only looking for the homepage design at this stage, but we may work with the selected designer on additional pages later.
Deliverables:
Homepage design in layered PSD, Figma, or Adobe XD format
Any fonts and assets used
Preview images/mockups
We look forward to seeing your ideas and working with a designer who can bring our brand to life with a fresh and functional homepage design.
Let us know if you have any questions.
Hobby Animal Keepers, Pet Owners
Animal Nutrition & Feed
2 page

```html
<!DOCTYPE html>
<html lang="en">
<head>
<meta charset="utf-8">
<title>Brenvik – Fish &amp; Chicken Food</title>
<link href="https://fonts.googleapis.com/css2?family=Ubuntu:wght@400;500;700&family=Lato:wght@400;700&family=Roboto:wght@400;500&display=swap" rel="stylesheet">
<style>
:root{
  --orange:#f7a441;
  --dark:#3c3c3b;
  --white:#ffffff;
  --ink:#2b2b2b;
  --peach:#fdf1e4;
  --muted:#555;
  --black:#111111;
  --line:#d9d9d9;
}
*{margin:0;padding:0;box-sizing:border-box}
html,body{width:1200px;height:2777px;overflow:hidden;background:var(--white)}
body{position:relative;font-family:"Lato",sans-serif;color:var(--ink)}
.abs{position:absolute}
.h{font-family:"Ubuntu",sans-serif}
.topbar{top:0;left:0;width:1200px;height:43px;font-size:15px}
.topbar .ship{left:111px;top:11px;font-weight:700}
.topbar .contact{left:663px;top:12px;font-family:"Ubuntu",sans-serif;font-weight:500}
.topbar .sep{left:759px;top:6px;width:1px;height:30px;background:var(--line)}
.repeat{left:777px;top:6px;width:140px;height:29px;border-radius:15px;background:var(--orange);color:var(--white);font-size:14px;font-weight:700;display:flex;align-items:center;justify-content:center;gap:6px}
.topbar .sep2{left:933px;top:6px;width:1px;height:30px;background:var(--line)}
.account{left:952px;top:10px;display:flex;align-items:center;gap:10px;font-family:"Ubuntu",sans-serif;font-size:15px}
.header{top:43px;left:0;width:1200px;height:86px;background:var(--dark)}
.logo{left:111px;top:20px;display:flex;align-items:center;gap:4px;color:var(--white);font-family:"Ubuntu",sans-serif;font-weight:700;font-size:46px;line-height:1}
.logo i{display:block;width:40px;height:40px;border-radius:50%;background:var(--orange)}
.search{left:413px;top:21px;width:393px;height:45px;background:var(--white);border-radius:23px;font-size:14px;padding:13px 22px;color:#333}
.search svg{position:absolute;right:22px;top:14px}
.shopnow{left:934px;top:21px;width:154px;height:45px;border-radius:23px;background:var(--orange);color:var(--white);font-family:"Ubuntu",sans-serif;font-weight:700;font-size:16px;display:flex;align-items:center;justify-content:center;gap:8px}
.nav{top:129px;left:0;width:1200px;height:48px;background:var(--peach);display:flex;gap:0;padding-left:110px;align-items:center;font-family:"Ubuntu",sans-serif;font-size:16px;color:#444}
.nav span{margin-right:36px}
.hero{left:103px;top:234px;width:654px;height:254px;background:var(--orange);border-radius:14px;overflow:hidden}
.hero h1{position:absolute;left:30px;top:30px;font-family:"Ubuntu",sans-serif;font-weight:700;font-size:48px;line-height:44px;color:var(--white)}
.hero p{position:absolute;left:30px;top:126px;width:290px;color:var(--white);font-size:15px;line-height:21px}
.pill{position:absolute;background:var(--white);color:var(--orange);border-radius:20px;font-family:"Ubuntu",sans-serif;font-weight:700;font-size:16px;display:flex;align-items:center;justify-content:center}
.hero .pill{left:30px;top:178px;width:118px;height:41px}
.hero-photo{position:absolute;left:390px;top:0;width:264px;height:254px;background:radial-gradient(ellipse at 55% 60%,#d9a15a 0%,#b08050 45%,rgba(247,164,65,0) 75%)}
.paw{position:absolute;border-radius:50%;background:var(--dark);border:5px solid var(--white)}
.promo{left:776px;top:234px;width:321px;height:254px;background:var(--dark);border-radius:14px}
.promo .tag{position:absolute;left:22px;top:26px;width:98px;height:26px;border-radius:13px;background:var(--orange);color:var(--white);font-family:"Ubuntu",sans-serif;font-weight:700;font-size:15px;display:flex;align-items:center;justify-content:center}
.promo .orig{position:absolute;left:128px;top:29px;color:var(--white);font-family:"Ubuntu",sans-serif;font-weight:500;font-size:16px}
.promo h2{position:absolute;left:32px;top:68px;color:var(--white);font-family:"Ubuntu",sans-serif;font-weight:700;font-size:32px;line-height:32px}
.promo p{position:absolute;left:32px;top:142px;width:170px;color:var(--white);font-size:14px;line-height:20px}
.promo .pill{left:32px;top:195px;width:111px;height:35px;font-size:15px}
.promo .pack{position:absolute;left:205px;top:68px;width:80px;height:145px;border-radius:8px;background:linear-gradient(160deg,#3aa9a0,#2c6f6b)}
.promo .pct{position:absolute;left:252px;top:32px;width:52px;height:52px;border-radius:50%;background:var(--orange);color:var(--white);font-family:"Ubuntu",sans-serif;font-weight:700;font-size:28px;display:flex;align-items:center;justify-content:center}
.dots{left:189px;top:512px;display:flex;gap:8px;align-items:center}
.dots b{width:14px;height:14px;border-radius:50%;border:2px solid var(--orange)}
.dots b.on{background:var(--orange)}
.tagline{top:585px;left:96px;width:1008px;display:flex;align-items:center;gap:8px}
.tagline hr{flex:1;border:0;border-top:1px solid var(--line)}
.tagline h2{font-family:"Ubuntu",sans-serif;font-weight:500;font-size:28px;color:#333}
.subline{top:636px;left:0;width:1200px;text-align:center;font-family:"Ubuntu",sans-serif;font-size:18px;color:#333}
.usps{top:699px;left:0;width:1200px;height:149px;background:var(--peach)}
.usp{position:absolute;top:41px;display:flex;gap:9px;align-items:center}
.usp .ic{width:65px;height:65px;border-radius:50%;display:flex;align-items:center;justify-content:center}
.usp h3{font-family:"Ubuntu",sans-serif;font-weight:500;font-size:18px;margin-bottom:6px}
.usp p{font-family:"Ubuntu",sans-serif;font-size:15px;color:#333}
.sec-title{font-family:"Ubuntu",sans-serif;font-weight:500;font-size:34px;color:#333}
.more{font-family:"Ubuntu",sans-serif;font-weight:500;font-size:16px;display:flex;gap:10px;align-items:center;color:#222}
.cat{position:absolute;top:985px;width:186px}
.cat .bg{position:absolute;top:31px;left:0;width:186px;height:118px;border-radius:10px}
.cat .pouch{position:absolute;top:0;left:50px;width:90px;height:135px;border-radius:6px;background:linear-gradient(180deg,#d8407f,#a5296a)}
.cat span{position:absolute;top:165px;left:0;width:186px;text-align:center;font-family:"Ubuntu",sans-serif;font-size:18px;color:#333}
.deal{position:absolute;top:1323px;width:313px;height:190px;overflow:hidden}
.deal h3{position:absolute;left:20px;top:55px;font-family:"Lato",sans-serif;font-weight:700;font-size:24px}
.deal p{position:absolute;left:21px;top:91px;width:170px;font-size:16px;line-height:24px}
.card{position:absolute;top:1648px;width:228px;text-align:center}
.card .box{height:255px;background:#f4f4f4;border-radius:4px;position:relative;box-shadow:0 0 3px rgba(0,0,0,.06)}
.card .pack{position:absolute;left:65px;top:40px;width:115px;height:178px;border-radius:4px}
.card .stars{margin-top:30px;height:18px}
.card h4{margin-top:12px;font-family:"Ubuntu",sans-serif;font-weight:500;font-size:20px}
.card .price{margin-top:10px;font-family:"Ubuntu",sans-serif;font-weight:500;font-size:18px}
.sale{left:111px;top:2095px;width:977px;height:191px;background:#aedde8;border-radius:12px}
.sale h2{position:absolute;left:61px;top:50px;font-family:"Ubuntu",sans-serif;font-weight:700;font-size:34px;color:#222}
.sale p{position:absolute;left:61px;top:106px;font-size:19px;line-height:27px;color:#333}
.sale-dog{left:830px;top:2065px;width:170px;height:221px;border-radius:90px 90px 0 0;background:linear-gradient(180deg,#6b6b6b,#9a9a9a 60%,#cfcfcf)}
.footer{top:2387px;left:0;width:1200px;height:390px;background:var(--black);color:var(--white);font-family:"Roboto",sans-serif}
.fcol{position:absolute;top:42px}
.fcol h5{font-weight:400;font-size:17px;padding-bottom:12px;position:relative}
.fcol h5::after{content:"";position:absolute;left:0;bottom:0;width:50px;height:2px;background:var(--white)}
.fcol ul{list-style:none;margin-top:22px;font-size:17px;line-height:31px}
.fcol li{display:flex;gap:14px}
.fcol li svg{flex:none;margin-top:9px}
.cards{display:flex;gap:8px;margin-top:22px}
.cards i{width:43px;height:26px;border-radius:3px}
.frule{left:111px;top:319px;width:977px;height:1px;background:#3a3a3a}
.copy{top:342px;left:0;width:1200px;text-align:center;font-size:17px}
</style>
</head>
<body>

<div class="abs topbar">
  <div class="abs ship">Free shipping from €29</div>
  <div class="abs contact">Contact Us</div>
  <div class="abs sep"></div>
  <div class="abs repeat">Repeat Order
    <svg width="16" height="16" viewBox="0 0 16 16" fill="none" stroke="#fff" stroke-width="2"><path d="M13 8a5 5 0 1 1-2-4"/><path d="M11 1v3h3"/></svg>
  </div>
  <div class="abs sep2"></div>
  <div class="abs account">
    <svg width="18" height="18" viewBox="0 0 18 18" fill="none" stroke="#333" stroke-width="1.6"><circle cx="9" cy="6" r="4"/><path d="M2 17c0-4 3-6 7-6s7 2 7 6z"/></svg>
    <span>My Brenvik</span>
    <svg width="12" height="8" viewBox="0 0 12 8" fill="none" stroke="#333" stroke-width="1.6"><path d="M1 1l5 5 5-5"/></svg>
  </div>
</div>

<header class="abs header">
  <div class="abs logo"><i></i>brenvik</div>
  <div class="abs search">Searching For...
    <svg width="18" height="18" viewBox="0 0 18 18" fill="none" stroke="#222" stroke-width="2.4"><circle cx="7.5" cy="7.5" r="5.5"/><path d="M12 12l4.5 4.5"/></svg>
  </div>
  <div class="abs shopnow">
    <svg width="18" height="16" viewBox="0 0 18 16" fill="#fff"><path d="M0 1h3l3 9h9l2-7H5l-.6-2H0z"/><circle cx="7" cy="14" r="1.6"/><circle cx="14" cy="14" r="1.6"/></svg>
    Shop Now
  </div>
</header>

<nav class="abs nav">
  <span>Fishing</span><span>Birds</span><span>Dogs</span><span>Chickens</span><span>Rodent</span><span>Angling</span><span>Reptiles</span><span>Farm animals</span><span>Other Products</span><span>Garden animals</span>
</nav>

<section class="abs hero">
  <h1>Welcome To<br>Brenvik</h1>
  <p>Lorem ipsum dolor sit amet, consectetur adipiscing elit, sed do eiusmod tempor</p>
  <div class="pill">Shop Now</div>
  <div class="hero-photo" role="img" aria-label="Golden retriever and grey cat sitting together"></div>
</section>
<div class="paw" style="left:428px;top:212px;width:72px;height:72px"></div>
<div class="paw" style="left:620px;top:210px;width:52px;height:52px"></div>
<div class="paw" style="left:441px;top:364px;width:58px;height:58px"></div>

<section class="abs promo">
  <div class="tag">Brenvik</div>
  <div class="orig">Originals</div>
  <h2>Premium<br>Voer.</h2>
  <p>Excepteur sint occaecat cupidatat non proident,</p>
  <div class="pill">Shop Now</div>
  <div class="pack" role="img" aria-label="Teal pet food bag labelled best food"></div>
  <div class="pct">%</div>
</section>

<div class="abs dots">
  <svg width="16" height="16" viewBox="0 0 16 16"><path d="M1 0l15 8-15 8z" fill="#f7a441"/></svg>
  <b></b><b></b><b></b><b class="on"></b><b></b><b></b><b></b>
</div>

<div class="abs tagline"><hr><h2>Everything for my pet. My number one choice.</h2><hr></div>
<div class="abs subline">Brenvik - Sells fish and chicken food</div>

<section class="abs usps">
  <div class="usp" style="left:111px">
    <div class="ic" style="background:var(--orange)"><svg width="32" height="32" viewBox="0 0 32 32" fill="none" stroke="#fff" stroke-width="4"><path d="M6 14a10 10 0 0 1 18-5"/><path d="M26 18a10 10 0 0 1-18 5"/><path d="M25 3v7h-7" stroke-width="3"/><path d="M7 29v-7h7" stroke-width="3"/></svg></div>
    <div><h3>Save 10% on repeat orders</h3><p>Discover BrenvikConvenience &nbsp;→</p></div>
  </div>
  <div class="usp" style="left:475px">
    <div class="ic" style="background:var(--dark)"><svg width="30" height="30" viewBox="0 0 30 30" fill="#fff"><rect x="5" y="12" width="20" height="15"/><rect x="3" y="8" width="24" height="5"/><rect x="14" y="8" width="2" height="19" fill="#3c3c3b"/></svg></div>
    <div><h3>Collect &amp; receive gifts</h3><p>Start saving &nbsp;→</p></div>
  </div>
  <div class="usp" style="left:784px">
    <div class="ic" style="background:var(--black)"><svg width="30" height="30" viewBox="0 0 30 30" fill="#fff"><circle cx="15" cy="9" r="5"/><path d="M5 26c0-6 4-9 10-9s10 3 10 9z"/></svg></div>
    <div><h3>Get advice from an expert</h3><p>Read our magazine &nbsp;→</p></div>
  </div>
</section>

<h2 class="abs sec-title" style="left:111px;top:910px">Shop for your Category</h2>
<div class="cat" style="left:113px"><div class="bg" style="background:#f7e690"></div><div class="pouch" role="img" aria-label="Cat food pouch"></div><span>Fish Food</span></div>
<div class="cat" style="left:310px"><div class="bg" style="background:#a6d9e8"></div><div class="pouch" role="img" aria-label="Cat food pouch" style="background:linear-gradient(180deg,#e0473f,#b32c2c)"></div><span>Chicken Food</span></div>
<div class="cat" style="left:508px"><div class="bg" style="background:#acdf86"></div><div class="pouch" role="img" aria-label="Cat food pouch"></div><span>Accessories</span></div>
<div class="cat" style="left:705px"><div class="bg" style="background:#e6e6e6"></div><div class="pouch" role="img" aria-label="Cat food pouch" style="background:linear-gradient(180deg,#f07f3a,#d45b2a)"></div><span>Fish Food</span></div>
<div class="cat" style="left:902px"><div class="bg" style="background:#f3c0c8"></div><div class="pouch" role="img" aria-label="Cat food pouch" style="background:linear-gradient(180deg,#e0473f,#b32c2c)"></div><span>Chicken Food</span></div>

<h2 class="abs sec-title" style="left:111px;top:1250px">This week's best deals</h2>
<div class="abs more" style="left:934px;top:1260px">All special offers
  <svg width="20" height="14" viewBox="0 0 20 14" fill="none" stroke="#222" stroke-width="2"><path d="M0 7h18M12 1l6 6-6 6"/></svg></div>
<div class="deal" style="left:111px;background:linear-gradient(90deg,#f2efe9 45%,#c79b6c 80%,#ece6dc)" role="img" aria-label="Paper feed bag with fish and spices">
  <h3>Free Shipping</h3><p>On orders over €50 within the Netherlands</p></div>
<div class="deal" style="left:444px;background:linear-gradient(90deg,#4a4a4a,#6d6d6d 60%,#e9e4da 70%,#d8d0c0)" role="img" aria-label="Feed sack with a chicken and grain" >
  <h3 style="color:#fff">Fast Delivery</h3><p style="color:#eee">Receive your order within 24–48 hours</p></div>
<div class="deal" style="left:775px;background:linear-gradient(100deg,#8d8d8d,#b9b6b2 55%,#d8cfc4)" role="img" aria-label="Cat beside bowls of dry food">
  <h3 style="color:#fff">Top Quality Feed</h3><p style="color:#f4f4f4;width:190px">Carefully selected from trusted European</p></div>

<h2 class="abs sec-title" style="left:111px;top:1590px">Featured Products</h2>
<div class="abs more" style="left:924px;top:1600px">View All Products
  <svg width="20" height="14" viewBox="0 0 20 14" fill="none" stroke="#222" stroke-width="2"><path d="M0 7h18M12 1l6 6-6 6"/></svg></div>

<div class="card" style="left:111px"><div class="box"><div class="pack" role="img" aria-label="Blue cat food pack" style="background:linear-gradient(180deg,#2f7fc4,#1d5ea0)"></div></div>
  <svg class="stars" width="90" height="18" viewBox="0 0 90 18"><g fill="#f7a441"><path id="s" d="M9 1l2.4 5 5.6.6-4.2 3.8 1.2 5.6L9 13.2 4 16l1.2-5.6L1 6.6 6.6 6z"/><use href="#s" x="18"/><use href="#s" x="36"/><use href="#s" x="54"/></g><use href="#s" x="72" fill="none" stroke="#f7a441" stroke-width="1.2"/></svg>
  <h4>Other Animal Feed</h4><div class="price">€2.29</div></div>
<div class="card" style="left:361px"><div class="box"><div class="pack" role="img" aria-label="Teal cat food pack" style="background:linear-gradient(180deg,#2aa58f,#1c7d6b)"></div></div>
  <svg class="stars" width="90" height="18" viewBox="0 0 90 18"><g fill="#f7a441"><use href="#s"/><use href="#s" x="18"/><use href="#s" x="36"/><use href="#s" x="54"/></g><use href="#s" x="72" fill="none" stroke="#f7a441" stroke-width="1.2"/></svg>
  <h4>Other Animal Feed</h4><div class="price">€2.29</div></div>
<div class="card" style="left:611px"><div class="box"><div class="pack" role="img" aria-label="Blue cat food pack" style="background:linear-gradient(180deg,#2f7fc4,#1d5ea0)"></div></div>
  <svg class="stars" width="90" height="18" viewBox="0 0 90 18"><g fill="#f7a441"><use href="#s"/><use href="#s" x="18"/><use href="#s" x="36"/><use href="#s" x="54"/></g><use href="#s" x="72" fill="none" stroke="#f7a441" stroke-width="1.2"/></svg>
  <h4>Other Animal Feed</h4><div class="price">€2.29</div></div>
<div class="card" style="left:862px"><div class="box"><div class="pack" role="img" aria-label="Blue cat food pack" style="background:linear-gradient(180deg,#2f7fc4,#1d5ea0)"></div></div>
  <svg class="stars" width="90" height="18" viewBox="0 0 90 18"><g fill="#f7a441"><use href="#s"/><use href="#s" x="18"/><use href="#s" x="36"/><use href="#s" x="54"/></g><use href="#s" x="72" fill="none" stroke="#f7a441" stroke-width="1.2"/></svg>
  <h4>Other Animal Feed</h4><div class="price">€2.29</div></div>

<section class="abs sale">
  <h2>Autumn Sale – Save Up to 20%!</h2>
  <p>Limited-time discounts on top-quality fish and chicken feed.<br>Don’t miss out!</p>
</section>
<div class="abs sale-dog" role="img" aria-label="Happy grey dog with tongue out"></div>

<footer class="abs footer">
  <div class="fcol" style="left:116px"><h5>QUICK LINKS</h5>
    <ul><li>Home</li><li>About</li><li>Services</li><li>Products</li><li>Contact Us</li></ul></div>
  <div class="fcol" style="left:304px"><h5>EXTRAS</h5>
    <ul style="line-height:30px"><li>Our Brands</li><li>Special Offers</li><li>Gift Vouchers</li><li>Affiliates</li></ul></div>
  <div class="fcol" style="left:537px"><h5>CONTACT US</h5>
    <ul style="line-height:30px">
      <li><svg width="14" height="14" viewBox="0 0 14 14" fill="none" stroke="#fff" stroke-width="1.6"><circle cx="7" cy="7" r="6"/><path d="M7 4v3h3"/></svg>Monday - Friday: 09:00 - 18:30</li>
      <li><svg width="14" height="14" viewBox="0 0 14 14" fill="#fff"><path d="M7 0a5 5 0 0 1 5 5c0 4-5 9-5 9S2 9 2 5a5 5 0 0 1 5-5z"/><circle cx="7" cy="5" r="2" fill="#111"/></svg>123 Company Name, demo<br>address</li>
      <li><svg width="14" height="14" viewBox="0 0 14 14" fill="#fff"><path d="M3 0l3 3-2 2c1 2 3 4 5 5l2-2 3 3-2 3C6 14 0 8 0 3z"/></svg>+123-456-789-0</li>
      <li><svg width="14" height="14" viewBox="0 0 14 14" fill="none" stroke="#fff" stroke-width="1.4"><rect x="1" y="2" width="12" height="10"/><path d="M1 3l6 5 6-5"/></svg>shop@companyname.com</li>
    </ul></div>
  <div class="fcol" style="left:906px"><h5>PAYMENT OPTIONS</h5>
    <div class="cards"><i style="background:#2d7cc3"></i><i style="background:#e9ecf2"></i><i style="background:#d3364a"></i></div></div>
  <div class="abs frule"></div>
  <div class="abs copy">© 2025 Company Name. All Rights Reserved.</div>
</footer>

</body>
</html>
```